Business Card for brovaLINK

Create a Business Card with an existing logo for brovaLINK AG. We are a Information Technology company that does consulting and developing SW to automate business processes. The main colors are given from the logo.

Industry/Entity Type

Business

Requirements
Nice to have
• we use a a font style Century Gothic in our documents

```html
<!DOCTYPE html>
<html lang="en">
<head>
<meta charset="utf-8">
<title>brovaLINK Business Card</title>
<link href="https://fonts.googleapis.com/css2?family=Didact+Gothic&display=swap" rel="stylesheet">
<style>
  :root {
    --bg: #e6e4e1;
    --card: #ffffff;
    --ink: #1e1e1e;
    --band: #141414;
    --accent-blue: #2e6fc0;
    --muted: #5a5a5a;
    --light: #f2f2f2;
  }
  * { box-sizing: border-box; margin: 0; padding: 0; }
  html, body {
    width: 1200px; height: 1054px; overflow: hidden;
    background: var(--bg);
    font-family: "Didact Gothic", "Century Gothic", sans-serif;
  }
  .canvas { position: relative; width: 1200px; height: 1054px; }
  .card {
    position: absolute; left: 190px; width: 820px; height: 469px;
    background: var(--card);
    box-shadow: 0 8px 24px rgba(0,0,0,0.18);
    overflow: hidden;
  }
  .card--front { top: 40px; }
  .card--back { top: 545px; }

  .wordmark {
    display: flex; align-items: center; gap: 18px;
    color: var(--ink);
  }
  .wordmark__mark {
    width: 22px; height: 22px;
    background: var(--accent-blue);
    flex: none;
  }
  .wordmark__name {
    font-size: 44px; line-height: 1;
    letter-spacing: 8px; text-transform: uppercase;
  }

  .card--front .wordmark {
    position: absolute; left: 50%; top: 50%;
    transform: translate(-50%, -50%);
  }

  .back-band { position: absolute; inset: 0; }
  .card--back .wordmark { position: absolute; left: 44px; top: 198px; gap: 14px; }
  .card--back .wordmark__mark { width: 18px; height: 18px; }
  .card--back .wordmark__name { font-size: 32px; letter-spacing: 5px; }

  .person { position: absolute; right: 40px; top: 44px; text-align: right; }
  .person__name { color: var(--accent-blue); font-size: 22px; letter-spacing: 1.5px; }
  .person__title { color: var(--muted); font-size: 15px; letter-spacing: 2px; margin-top: 4px; }

  .address {
    position: absolute; right: 40px; top: 178px; text-align: right;
    color: var(--light); font-size: 15px; line-height: 24px; letter-spacing: 0.5px;
  }

  .contacts {
    position: absolute; left: 40px; top: 306px; list-style: none;
    color: var(--light); font-size: 13px; letter-spacing: 0.5px;
  }
  .contacts li { display: flex; align-items: center; gap: 10px; height: 22px; }
  .contacts svg { width: 13px; height: 13px; fill: var(--light); flex: none; }
</style>
</head>
<body>
<main class="canvas">
  <section class="card card--front">
    <div class="wordmark">
      <span class="wordmark__mark"></span>
      <span class="wordmark__name">brovaLINK</span>
    </div>
  </section>

  <section class="card card--back">
    <svg class="back-band" width="820" height="469" viewBox="0 0 820 469" aria-hidden="true">
      <path d="M0 290 H340 V150 H820 V428 H0 Z" fill="var(--band)"/>
    </svg>

    <div class="person">
      <p class="person__name">DANIEL WEBER</p>
      <p class="person__title">GENERAL MANAGER</p>
    </div>

    <div class="wordmark">
      <span class="wordmark__mark"></span>
      <span class="wordmark__name">brovaLINK</span>
    </div>

    <div class="address">
      <p>Seestrasse 198</p>
      <p>3rd Floor, 8002 Zürich</p>
    </div>

    <ul class="contacts">
      <li><svg viewBox="0 0 16 16"><path d="M3 1l3 3-2 2c1 2 3 4 5 5l2-2 3 3-2 3C6 15 1 10 1 3z"/></svg>044 210 7300</li>
      <li><svg viewBox="0 0 16 16"><path d="M4 0h8v16H4zM5.5 2v10h5V2zM7 13.5h2v1H7z" fill-rule="evenodd"/></svg>079 210 7300</li>
      <li><svg viewBox="0 0 16 16"><path d="M4 1h7v4h3v10H2V5h2zM5 2v4h5V2zM4 8h2v2H4zm3 0h2v2H7zm3 0h2v2h-2z"/></svg>044 210 7301</li>
      <li><svg viewBox="0 0 16 16"><path d="M1 3h14v10H1zM2 4l6 5 6-5z" fill-rule="evenodd"/></svg>info@brovalink.ch</li>
      <li><svg viewBox="0 0 16 16"><path d="M8 1a7 7 0 100 14A7 7 0 008 1zm0 1.5c1 1 1.6 2.6 1.7 4.5H6.3C6.4 5.1 7 3.5 8 2.5zM2.6 7h2.3c.1-1.6.5-3 1.2-4A5.5 5.5 0 002.6 7zm8.5 0h2.3A5.5 5.5 0 009.9 3c.7 1 1.1 2.4 1.2 4zM2.6 9a5.5 5.5 0 003.5 4c-.7-1-1.1-2.4-1.2-4zm3.7 0c.1 1.9.7 3.5 1.7 4.5 1-1 1.6-2.6 1.7-4.5zm4.8 0c-.1 1.6-.5 3-1.2 4a5.5 5.5 0 003.5-4z"/></svg>www.brovalink.ch</li>
    </ul>
  </section>
</main>
</body>
</html>
```